Harvest Gateway Fellowship Ministries needs a fresh new web design

We are an up and coming multicultural church that aims to bring people into a life changing encounter with God. We need a fresh and inviting website in order to increase our internet presence and make us easier to connect with.
Here are some of the basic requirements for the site:
• Clearly displayed address, service times, and contact info
• A staff profile page
• An area for a calendar with upcoming events and their details
• Social media buttons
• Group pages for the different ministries (youth, children’s church, men, etc…)
• An area for donations and eCommerce
• A resources page for assorted media (podcasts, sermons, videos, etc.…)
• An area for prayer requests.

```html
<!DOCTYPE html>
<html lang="en">
<head>
<meta charset="utf-8">
<title>Harvest Gateway Fellowship Ministries</title>
<link href="https://fonts.googleapis.com/css2?family=Cinzel:wght@400;700&family=Arimo:ital,wght@0,400;0,700;1,400&display=swap" rel="stylesheet">
<style>
:root{
  --navy:#3c536d;
  --navy-dark:#2f4660;
  --ink:#4a4a4a;
  --muted:#6d6d6d;
  --title:#2e4a6b;
  --gold:#c9a23a;
  --gold-dark:#9c7a22;
  --white:#ffffff;
  --line:#c9c9c9;
}
*{box-sizing:border-box;margin:0;padding:0}
html,body{width:1034px;height:1200px;overflow:hidden}
body{
  position:relative;
  font-family:"Arimo",Arial,sans-serif;
  color:var(--ink);
  background:linear-gradient(180deg,#1b2f4f 0%,#2a4566 14%,#3f6680 24%,#8c8a95 35%,#c49786 44%,#dcb396 56%,#e8c9a8 75%,#eccfae 100%);
}
.abs{position:absolute}
.serif{font-family:"Cinzel",Georgia,serif}

/* header */
.contact{left:149px;top:80px;color:var(--white);font-size:10px}
.contact h3,.times h3{font-family:"Cinzel",Georgia,serif;font-weight:400;font-size:14px;letter-spacing:1px;margin-bottom:8px}
.contact p{margin-bottom:12px}
.contact .row{display:flex;gap:18px;align-items:center}
.contact .row span{display:flex;align-items:center;gap:5px}
.times{left:658px;top:66px;color:var(--white);font-size:9.5px;line-height:18.5px}
.times h3{margin-bottom:2px}
.brand{left:436px;top:30px;width:160px;text-align:center}
.brand .mark{width:34px;height:34px;border-radius:50%;background:var(--gold);margin:0 auto 8px;box-shadow:none}
.brand .name{font-family:"Cinzel",Georgia,serif;font-weight:700;font-size:10px;line-height:13px;color:#f2d06b;letter-spacing:.5px}

/* main panel */
.panel{left:148px;top:163px;width:739px;height:942px;background:var(--white);box-shadow:0 0 6px rgba(0,0,0,.15)}
.nav{left:157px;top:172px;width:720px;height:36px;background:var(--navy);display:flex}
.nav a{color:var(--white);font-size:9.5px;text-decoration:none;display:flex;align-items:center;justify-content:center;border-right:1px solid #546a82;height:100%}
.nav a:last-child{border-right:none}
.hero{left:157px;top:216px;width:720px;height:324px;background:radial-gradient(ellipse at 55% 45%,#8a6a44 0%,#5c4430 30%,#2e2520 65%,#1c1815 100%)}
.caption{left:157px;top:426px;width:362px;height:98px;background:rgba(30,26,22,.82);color:var(--white);padding:16px 18px}
.caption h2{font-family:"Cinzel",Georgia,serif;font-weight:400;font-size:13.5px;letter-spacing:.4px;margin-bottom:10px}
.caption p{font-size:9.6px;line-height:19px}
.arrows{left:826px;top:508px;display:flex;gap:1px}
.arrows span{width:20px;height:20px;background:rgba(90,80,70,.8);display:flex;align-items:center;justify-content:center}

/* welcome */
.welcome-img{left:157px;top:566px;width:212px;height:138px;background:linear-gradient(90deg,#e9c36a 0%,#caa45a 40%,#b89555 70%,#e4bf6a 100%)}
.welcome{left:391px;top:571px;width:490px}
.welcome h1{font-family:"Cinzel",Georgia,serif;font-weight:400;color:var(--title);font-size:22px;letter-spacing:.5px;line-height:24px}
.welcome h2{font-family:"Cinzel",Georgia,serif;font-weight:400;color:var(--title);font-size:15px;letter-spacing:.3px;margin:4px 0 11px}
.welcome p{font-size:8.8px;line-height:17.8px;color:var(--muted);padding-left:2px}
.divider{left:157px;top:726px;width:720px;height:1px;background:var(--line)}

/* calendar */
.calendar{left:157px;top:754px;width:222px;height:213px;background:var(--navy);color:var(--white)}
.calendar .close{position:absolute;right:6px;top:3px;font-size:11px;color:#9fb3c8}
.calendar .month{position:absolute;left:26px;top:22px;width:170px;text-align:center;font-size:8px;border-bottom:1px solid #8da0b4;padding-bottom:5px}
.calendar .month i{color:#9bbf3a;font-style:normal}
.calendar .next{position:absolute;left:191px;top:22px;font-size:8px;color:#9bbf3a}
.grid{position:absolute;left:16px;top:50px;display:grid;grid-template-columns:repeat(7,27.5px);row-gap:0;font-size:8px;text-align:center}
.grid b{font-weight:700;height:20px}
.grid span{height:18px;line-height:18px}
.grid .dim{color:#8ea2b6}
.grid .today{outline:1px solid #8ea2b6;outline-offset:-1px;width:18px;margin:0 auto;color:#8ea2b6}
.calendar .hint{position:absolute;left:17px;top:168px;font-family:"Cinzel",Georgia,serif;font-size:9px;line-height:16px;letter-spacing:.2px}

/* events */
.events{left:398px;top:758px;width:262px}
.section-title{font-family:"Cinzel",Georgia,serif;font-weight:400;color:var(--title);font-size:13px;letter-spacing:.8px}
.event{position:absolute;left:4px;width:232px;height:95px;border-bottom:1px solid var(--line)}
.event .thumb{position:absolute;left:0;top:0;width:63px;height:59px}
.event h4{position:absolute;left:76px;top:0;font-family:"Cinzel",Georgia,serif;font-weight:400;font-size:9px;color:#222;letter-spacing:.3px}
.event em{position:absolute;left:76px;top:17px;font-size:8px;color:var(--title)}
.event p{position:absolute;left:76px;top:33px;font-size:8.6px;line-height:16.5px;color:var(--muted);width:160px}
.scroll{left:656px;top:790px;width:5px;height:176px;background:#e4e4e4;border-radius:3px}
.scroll i{position:absolute;left:0;top:81px;width:5px;height:38px;background:#c2c2c2;border-radius:3px}

/* prayer form */
.prayer{left:682px;top:755px;width:195px}
.field{position:absolute;height:21px;border:1px solid #b9b9b9;font-size:8.8px;color:#6a6a6a;padding:5px 10px}
.send{position:absolute;left:0;top:170px;width:195px;height:30px;background:var(--navy);border-bottom:2px solid #1f3047;color:var(--white);font-family:"Cinzel",Georgia,serif;font-size:12px;letter-spacing:1px;text-align:center;line-height:29px}

/* donation banner */
.donate{left:157px;top:993px;width:720px;height:103px;background:linear-gradient(90deg,#111 0%,#1b1712 45%,#4a3a1c 68%,#a9822e 82%,#3a2e18 100%)}
.donate .frame{position:absolute;left:6px;top:6px;right:6px;bottom:6px;border:3px solid rgba(120,120,120,.55)}
.donate h2{position:absolute;left:35px;top:24px;font-family:"Cinzel",Georgia,serif;font-weight:400;font-size:17.5px;color:var(--white);letter-spacing:.8px}
.donate p{position:absolute;left:36px;top:55px;font-family:"Cinzel",Georgia,serif;font-size:13px;color:var(--white);letter-spacing:.5px}
.donate .btn{position:absolute;left:309px;top:52px;width:115px;height:23px;background:var(--gold-dark);color:var(--white);font-family:"Cinzel",Georgia,serif;font-size:11px;letter-spacing:.5px;text-align:center;line-height:23px}

/* footer */
.footer-nav{left:153px;top:1124px;display:flex;gap:24px;font-size:9px;color:#4a4a4a}
.copy{left:153px;top:1149px;font-size:8.8px;color:#4a4a4a}
.social{left:741px;top:1129px;display:flex;gap:6px}
.social span{width:24px;height:24px;border-radius:50%;background:#8a8480}
.code{left:965px;top:1136px;font-size:9px;color:#6a6a6a}
</style>
</head>
<body>

<div class="abs contact">
  <h3>Contact Info</h3>
  <p>Street name, State name, Country name.</p>
  <div class="row">
    <span><svg width="11" height="8" viewBox="0 0 11 8"><rect x=".5" y=".5" width="10" height="7" fill="#fff"/><path d="M.5 .5 5.5 4.5 10.5 .5" fill="none" stroke="#2a4566" stroke-width="1"/></svg>info@harvestgateway.org</span>
    <span><svg width="7" height="11" viewBox="0 0 7 11"><rect x=".6" y=".6" width="5.8" height="9.8" rx="1" fill="none" stroke="#fff" stroke-width="1.2"/><rect x="2.5" y="8.4" width="2" height="1" fill="#fff"/></svg>555.014.2280</span>
  </div>
</div>

<div class="abs brand">
  <div class="mark"></div>
  <div class="name">Harvest Gateway<br>Fellowship Ministries</div>
</div>

<div class="abs times">
  <h3>Service Times</h3>
  <div>Sunday 10:00 am Sunday School Kids For Christ</div>
  <div>10:00 am Adults Class</div>
  <div>Sunday Worship: 11:00 am ( &amp; ) Friday: Prayer 7:30pm</div>
</div>

<div class="abs panel"></div>

<nav class="abs nav">
  <a href="#" style="width:88px">HOME</a>
  <a href="#" style="width:85px">ABOUT US</a>
  <a href="#" style="width:75px">EVENTS</a>
  <a href="#" style="width:124px">PRAYER REQUEST</a>
  <a href="#" style="width:75px">DONATE</a>
  <a href="#" style="width:96px">RESOURCES</a>
  <a href="#" style="width:92px">OUR STAFF</a>
  <a href="#" style="width:85px">CONTACT US</a>
</nav>

<div class="abs hero" role="img" aria-label="Photo of weathered hands holding an open Bible"></div>
<div class="abs caption">
  <h2>Harvest Gateway Fellowship Ministries</h2>
  <p>a place where we can come together and fellowship. HGFM is located in Millbrook, New York and we would love to have you worship with us.</p>
</div>
<div class="abs arrows">
  <span><svg width="6" height="9" viewBox="0 0 6 9"><path d="M5 .5 1 4.5 5 8.5" fill="none" stroke="#bbb"/></svg></span>
  <span><svg width="6" height="9" viewBox="0 0 6 9"><path d="M1 .5 5 4.5 1 8.5" fill="none" stroke="#bbb"/></svg></span>
</div>

<div class="abs welcome-img" role="img" aria-label="Photo of the pastoral couple on a golden background"></div>
<div class="abs welcome">
  <h1>Welcome to</h1>
  <h2>Harvest Gateway Fellowship Ministries</h2>
  <p>Welcome to Harvest Gateway Fellowship Ministries, a place where we can come together and fellowship. HGFM is located in Millbrook, New York and we would love to have you worship with us. We believe God is doing something extraordinary through our church and would like for you to be a part. Please prayerfully consider our church as a place you would like to worship and fellowship with us as we continue to grow.</p>
</div>
<div class="abs divider"></div>

<div class="abs calendar">
  <span class="close">✕</span>
  <div class="month">JUNE <i>•</i> 2014</div>
  <span class="next">▶</span>
  <div class="grid">
    <b>MON</b><b>TUE</b><b>WED</b><b>THU</b><b>FRI</b><b>SUT</b><b>SUN</b>
    <span>1</span><span>2</span><span>3</span><span>4</span><span>5</span><span>6</span><span>7</span>
    <span>8</span><span class="dim">9</span><span class="dim">10</span><span class="dim">11</span><span class="dim">12</span><span class="dim">13</span><span class="dim">14</span>
    <span class="dim">15</span><span class="today">16</span><span class="dim">17</span><span class="dim">18</span><span class="dim">19</span><span class="dim">20</span><span class="dim">21</span>
    <span class="dim">22</span><span class="dim">23</span><span class="dim">24</span><span class="dim">25</span><span class="dim">26</span><span class="dim">27</span><span class="dim">28</span>
    <span class="dim">29</span><span class="dim">30</span><span class="dim">31</span><span>1</span><span>2</span><span>3</span><span>4</span>
  </div>
  <div class="hint">Select your favorite day and get to know what's the event</div>
</div>

<div class="abs events">
  <h3 class="section-title">Upcoming Events</h3>
  <div class="event" style="top:35px">
    <div class="thumb" role="img" aria-label="Photo of a congregation gathered in a hall" style="background:linear-gradient(135deg,#6b4a44,#2a2220)"></div>
    <h4>Random Bible Verse</h4>
    <em>Upcoming - 16 June 2014</em>
    <p>uncover many web sites still in their infa ncy.Various versions have evolved</p>
  </div>
  <div class="event" style="top:130px">
    <div class="thumb" role="img" aria-label="Photo of a worship leader singing" style="background:linear-gradient(135deg,#8a6a60,#3a2a28)"></div>
    <h4>Random Bible Verse</h4>
    <em>Upcoming - 16 June 2014</em>
    <p>uncover many web sites still in their infa ncy.Various versions have evolved</p>
  </div>
</div>
<div class="abs scroll"><i></i></div>

<div class="abs prayer">
  <h3 class="section-title">Prayer Requests</h3>
  <div class="field" style="left:0;top:29px;width:195px">Name :</div>
  <div class="field" style="left:0;top:59px;width:195px">Email :</div>
  <div class="field" style="left:0;top:89px;width:92px">Date :</div>
  <div class="field" style="left:104px;top:89px;width:91px">Time :</div>
  <div class="field" style="left:0;top:119px;width:195px;height:43px">Comments</div>
  <div class="send">Send a Requests</div>
</div>

<div class="abs donate" role="img" aria-label="Sunset landscape with a person raising arms on a hill">
  <div class="frame"></div>
  <h2>Donations and eCommerce</h2>
  <p>We hope you will visit us real soon.</p>
  <div class="btn">Donate Now</div>
</div>

<div class="abs footer-nav">
  <span>Home</span><span>About Us</span><span>Events</span><span>Prayer Request</span><span>Donate</span><span>Resources</span><span>Our Staff</span><span>Contact Us</span>
</div>
<div class="abs copy">© Copyright 2014. HGFM. All rights reserved.</div>
<div class="abs social" aria-label="Social media links">
  <span></span><span></span><span></span><span></span><span></span>
</div>
<div class="abs code">C8</div>

</body>
</html>
```